Pebblebrook Plots - Online-only garden installation company

Online-only garden installation company. Our demographic is middle aged / suburban women, and we anticipate Facebook driving traffic to this website, as well as referrals from garden centers. The website must be very simple in design and function.

All orders will be placed through the website, including size of garden (3 options), location in yard, payment, and scheduling of installation date.

The website should employ a 3 step process:

Step 1: Select garden size. Either an 4' X 4', 8' X 4', or 12' X 4'.

Step 2: Select a location. We would like to use online maps to look up a US address, then "drag and drop" one of the garden sizes from step 1 to the location the customer would like us to install the garden at their home.

Step 3: Pick an installation date and pay. Using an online calendar the customer will pick a date, and then pay for the installation via credit card.

The website will be linked to an email account, PebblebrookPlots@mailvale.com to inform us of orders placed.

Target Market(s)

Our demographic is middle aged / suburban women, and we anticipate Facebook driving traffic to this website, as well as referrals from garden centers.

Industry/Entity Type

Coding

Number of Pages Required

Requirements
Must have
• Scheduling and payment options.

```html
<!DOCTYPE html>
<html lang="en">
<head>
<meta charset="utf-8">
<title>Pebblebrook Plots</title>
<link href="https://fonts.googleapis.com/css2?family=Lora:wght@400;700&family=Open+Sans:wght@400;600&display=swap" rel="stylesheet">
<style>
:root{
  --green:#3a7f3c;
  --green-text:#3b7a35;
  --orange:#e05a27;
  --ink:#333333;
  --muted:#666666;
  --rule:#e2e2e2;
  --footer:#353535;
  --white:#ffffff;
}
*{margin:0;padding:0;box-sizing:border-box}
html,body{width:810px;height:1200px;overflow:hidden;background:var(--white)}
body{position:relative;font-family:"Open Sans",Arial,sans-serif;color:var(--ink)}
.abs{position:absolute}

.main-nav{left:330px;top:9px;display:flex;gap:25px;font-family:"Lora",Georgia,serif;font-size:8.5px;letter-spacing:.2px;text-transform:uppercase}
.main-nav a{color:var(--ink);text-decoration:none}
.main-nav a.active{color:var(--orange)}

.hero{left:0;top:30px;width:810px;height:385px;background:linear-gradient(180deg,#d8c9a0 0%,#9aa86a 25%,#5d8a3a 55%,#4b7a30 80%,#6e8f45 100%)}
.hero-arrow{top:210px;width:16px;height:24px;background:rgba(0,0,0,.45)}
.hero-arrow svg{display:block;margin:5px auto}

.brand{left:89px;top:0;width:118px;height:115px;background:var(--white);box-shadow:0 1px 4px rgba(0,0,0,.2);display:flex;flex-direction:column;align-items:center;justify-content:center;gap:8px}
.brand-mark{width:16px;height:16px;border-radius:50%;background:var(--green)}
.brand-name{font-family:"Lora",Georgia,serif;font-weight:700;font-size:11px;color:var(--ink);text-align:center;line-height:1.2}

.steps{left:89px;top:329px;width:632px;height:183px;background:var(--green);color:var(--white)}
.step{position:absolute;top:16px}
.step-icon{height:22px}
.step-rule{position:absolute;top:27px;height:1px;background:rgba(255,255,255,.35)}
.step-title{font-family:"Lora",Georgia,serif;font-weight:700;font-size:12px;margin-top:14px}
.step-sub{font-family:"Lora",Georgia,serif;font-size:10px;text-transform:uppercase;margin-top:4px}
.step-text{font-size:7.6px;line-height:12px;margin-top:12px}
.cta{left:338px;top:498px;width:135px;height:30px;background:var(--orange);color:var(--white);font-family:"Lora",Georgia,serif;font-size:10.5px;text-transform:uppercase;display:flex;align-items:center;justify-content:center}

.section-title{font-family:"Lora",Georgia,serif;color:var(--green-text);font-size:17px;font-weight:400}
.welcome-title{left:0;width:810px;top:566px;text-align:center}
.welcome-text{left:89px;top:594px;width:632px;text-align:center;font-size:7.4px;line-height:13.6px;color:var(--muted)}
.rule{left:0;width:810px;height:1px;background:var(--rule)}

.gallery-title{left:89px;top:701px}
.pager{top:707px;width:16px;height:15px;border:1px solid #bbb}
.pager svg{display:block;margin:3px auto}
.shot{top:733px;width:151px;height:119px}

.testi-title{left:0;width:810px;top:925px;text-align:center}
.ghost{top:956px;height:113px;background:linear-gradient(90deg,rgba(240,240,240,0),#efefef)}
.ghost.right{background:linear-gradient(90deg,#efefef,rgba(240,240,240,0))}
.quote-card{left:181px;top:956px;width:437px;height:113px;border:1px solid #cfcfcf;border-radius:3px;text-align:center;padding:22px 18px 0}
.quote-text{font-size:8px;line-height:13px;color:var(--muted)}
.quote-by{font-size:9px;color:var(--ink);margin-top:7px}
.avatar{left:385px;top:1049px;width:40px;height:40px;border-radius:50%;background:#c9b7a4;border:3px solid var(--white);box-shadow:0 0 0 1px #ccc}

.footer{left:0;top:1135px;width:810px;height:65px;background:var(--footer);color:#cfcfcf;font-size:7px}
.footer-nav{position:absolute;left:89px;top:21px}
.footer-nav span{margin:0 5px;color:#888}
.copyright{position:absolute;left:89px;top:41px}
.social{position:absolute;left:593px;top:24px;display:flex;gap:6px}
.social i{display:block;width:17px;height:17px;border-radius:50%}
</style>
</head>
<body>

<div class="abs hero" role="img" aria-label="Photo of a sunlit cottage garden with flowers, a stone path and a small wooden house"></div>
<div class="abs hero-arrow" style="left:0"><svg width="7" height="14" viewBox="0 0 7 14"><path d="M6 1L1 7l5 6" stroke="#fff" fill="none"/></svg></div>
<div class="abs hero-arrow" style="left:794px"><svg width="7" height="14" viewBox="0 0 7 14"><path d="M1 1l5 6-5 6" stroke="#fff" fill="none"/></svg></div>

<div class="abs brand">
  <div class="brand-mark"></div>
  <div class="brand-name">Pebblebrook<br>Plots</div>
</div>

<nav class="abs main-nav">
  <a class="active" href="#">Home</a><a href="#">About Us</a><a href="#">Services</a><a href="#">Gallery</a><a href="#">Testimonials</a><a href="#">Contact Us</a>
</nav>

<section class="abs steps">
  <div class="step-rule" style="left:56px;width:158px"></div>
  <div class="step-rule" style="left:236px;width:206px"></div>
  <div class="step" style="left:19px;width:160px">
    <svg class="step-icon" width="28" height="22" viewBox="0 0 28 22" fill="#fff"><rect x="0" y="0" width="6" height="6"/><rect x="8" y="0" width="20" height="6"/><rect x="0" y="8" width="6" height="6"/><rect x="8" y="8" width="20" height="6"/><rect x="0" y="16" width="6" height="6"/><rect x="8" y="16" width="20" height="6"/></svg>
    <div class="step-title">STEP 1</div>
    <div class="step-sub">Location in yard</div>
    <p class="step-text">Select garden size.<br>Either an 4' X 4', 8' X 4', or 12' X 4'.</p>
  </div>
  <div class="step" style="left:195px;width:185px">
    <svg class="step-icon" width="32" height="22" viewBox="0 0 32 22"><rect x="1" y="1" width="30" height="20" fill="none" stroke="#fff" stroke-width="2"/><circle cx="16" cy="11" r="6.5" fill="#fff"/><path d="M14.5 8.5l2-1v7" stroke="#3a7f3c" stroke-width="1.6" fill="none"/></svg>
    <div class="step-title">STEP 2</div>
    <div class="step-sub">Payment</div>
    <p class="step-text">Select a location. We would like to use online maps to look up a US address, then "drag and drop" one of the garden sizes from step 1 to the location the customer would like us to install the garden at their home</p>
  </div>
  <div class="step" style="left:435px;width:182px">
    <svg class="step-icon" width="21" height="22" viewBox="0 0 21 22" fill="#fff"><rect x="0" y="3" width="21" height="19"/><rect x="4" y="0" width="2" height="5"/><rect x="15" y="0" width="2" height="5"/><g fill="#3a7f3c"><rect x="2" y="8" width="4" height="3"/><rect x="8.5" y="8" width="4" height="3"/><rect x="15" y="8" width="4" height="3"/><rect x="2" y="13" width="4" height="3"/><rect x="8.5" y="13" width="4" height="3"/><rect x="15" y="13" width="4" height="3"/><rect x="2" y="18" width="4" height="2.5"/><rect x="8.5" y="18" width="4" height="2.5"/></g></svg>
    <div class="step-title">STEP 3</div>
    <div class="step-sub">Scheduling of installation date</div>
    <p class="step-text" style="text-align:justify">Pick an installation date and pay. Using an online calendar the customer will pick a date, and then pay for the installation via credit card.</p>
  </div>
</section>
<div class="abs cta">Get Started Now</div>

<h1 class="abs section-title welcome-title">Welcome to Pebblebrook Plots</h1>
<p class="abs welcome-text">Donec tincidunt dui vel lectus venenatis lobortis. Proin imperdiet in nibh sed tempor. Nam tristique erat eros, vel molestie justo iaculis vel. Aenean risus dolor, rhoncus ac leo sed, congue mattis neque. Cras tristique massa vitae lorem condimentum fermentum. Nullam at dapibus lorem, et euismod odio. Nam faucibus, arcu vel placerat pulvinar, eros magna ullamcorper lectus, eget porta magna est vitae justo. Donec tortor odio, dictum et ultrices eu, fermentum in orci. Nam volutpat eget justo eget rhoncus. Aliquam ut dictum ligula. Suspendisse congue et sapien vel venenatis. Donec ut porta mauris, ut blandit purus.</p>

<div class="abs rule" style="top:673px"></div>

<h2 class="abs section-title gallery-title">Gallery</h2>
<div class="abs pager" style="left:684px"><svg width="5" height="8" viewBox="0 0 5 8"><path d="M4 0.5L1 4l3 3.5" stroke="#777" fill="none"/></svg></div>
<div class="abs pager" style="left:704px"><svg width="5" height="8" viewBox="0 0 5 8"><path d="M1 0.5L4 4 1 7.5" stroke="#777" fill="none"/></svg></div>
<div class="abs shot" style="left:89px;background:linear-gradient(180deg,#c9cdd0 0%,#6f8f55 45%,#6fb33a 100%)" role="img" aria-label="Photo of a wide mown lawn framed by trees"></div>
<div class="abs shot" style="left:249px;background:linear-gradient(135deg,#3f6b2a 0%,#c9b83a 35%,#8e8fb8 60%,#5c9e35 100%)" role="img" aria-label="Photo of curving flower beds beside a green lawn path"></div>
<div class="abs shot" style="left:409px;background:linear-gradient(160deg,#5c4a3a 0%,#7f9a45 45%,#4a3a2e 100%)" role="img" aria-label="Photo of hands planting a seedling in soil"></div>
<div class="abs shot" style="left:569px;background:linear-gradient(180deg,#6f9fd8 0%,#7fa646 40%,#5e9a30 100%)" role="img" aria-label="Photo of a garden lawn with a wooden table and chairs"></div>

<div class="abs rule" style="top:884px"></div>

<h2 class="abs section-title testi-title">Testimonials</h2>
<div class="abs ghost" style="left:70px;width:97px"><svg style="position:absolute;left:20px;top:50px" width="8" height="14" viewBox="0 0 8 14"><path d="M7 1L1 7l6 6" stroke="#bbb" fill="none"/></svg></div>
<div class="abs ghost right" style="left:632px;width:108px"><svg style="position:absolute;left:80px;top:50px" width="8" height="14" viewBox="0 0 8 14"><path d="M1 1l6 6-6 6" stroke="#bbb" fill="none"/></svg></div>
<blockquote class="abs quote-card">
  <p class="quote-text"><span style="font-family:Lora,serif;font-weight:700;font-size:14px;color:#999;vertical-align:-3px">&ldquo;</span> Cras blandit ipsum vitae laoreet dapibus. Aenean a sodales nisi, in vestibulum purus. Lorem ipsum dolor sit amet, consectetur adipiscing elit. Pellentesque ultrices, sapien sit amet facilisis condimentum, ex sem dictum odio, at placerat ex sem eget purus. <span style="font-family:Lora,serif;font-weight:700;font-size:14px;color:#999;vertical-align:-6px">&rdquo;</span></p>
  <p class="quote-by">~ Mara Linden</p>
</blockquote>
<div class="abs avatar" role="img" aria-label="Portrait of the customer"></div>

<footer class="abs footer">
  <div class="footer-nav">Home<span>|</span>About Us<span>|</span>Services<span>|</span>Gallery<span>|</span>Testimonials<span>|</span>Contact Us</div>
  <div class="copyright">Copyright &nbsp;©&nbsp; 2017 &nbsp;Company name. &nbsp;All rights reserved.</div>
  <div class="social" aria-label="Social links">
    <i style="background:#3b5a9a"></i><i style="background:#2aa3df"></i><i style="background:#d9412f"></i><i style="background:#c9252b"></i><i style="background:#d6322b"></i><i style="background:#4a7bb0"></i>
  </div>
</footer>

</body>
</html>
```